New business card/stationary for a consulting company

I am looking for a clean and very professional looking business card for my consulting company as well as corresponding stationary. I am uploading our logo. I like simple and powerful for the feel. No graphics but I am open on everything else. Below is my contact information but would like the final to be in a version I can add my employees information into and print. Thank you.

Daniel Whitcombe
dan@ferncliffadvisory.com
2870 North 9th Avenue, Summit Floor, Elm Ridge, Illinois 60531
www.ferncliffadvisory.com

Industry/Entity Type

Consulting

Contact Information for Business Card

Daniel Whitcombe
dan@ferncliffadvisory.com
www.ferncliffadvisory.com

Font styles to use
Serif
Sans Serif

Requirements
Must have
• Our logo and the business card details.
Nice to have
• our website www.ferncliffadvisory.com

```html
<!DOCTYPE html>
<html lang="en">
<head>
<meta charset="utf-8">
<title>Ferncliff Advisory — Business Card</title>
<link rel="stylesheet" href="https://fonts.googleapis.com/css2?family=Questrial&family=Open+Sans:wght@400;700&display=swap">
<style>
  :root {
    --page-bg: #e9eaee;
    --navy-deep: #0a0a6e;
    --navy-mid: #1010a0;
    --royal: #1f2fd0;
    --paper: #f7f7f8;
    --ink-navy: #20207a;
    --white: #ffffff;
  }
  * { margin: 0; padding: 0; box-sizing: border-box; }
  html, body {
    width: 1200px; height: 900px; overflow: hidden;
    background: var(--page-bg);
  }
  .canvas {
    position: relative; width: 1200px; height: 900px;
    display: flex; flex-direction: column; align-items: center; justify-content: center; gap: 56px;
  }
  .card {
    position: relative; width: 580px; height: 330px;
    box-shadow: 0 10px 28px rgba(20, 20, 60, 0.22);
    overflow: hidden;
  }

  /* Front */
  .card--front {
    background: linear-gradient(115deg, var(--royal) 0%, var(--navy-mid) 45%, var(--navy-deep) 100%);
    color: var(--white);
    display: flex; flex-direction: column; align-items: center; justify-content: center;
  }
  .brand {
    display: flex; align-items: center; gap: 14px;
    font-family: "Questrial", sans-serif; font-weight: 400;
    letter-spacing: 0.04em; text-transform: uppercase;
  }
  .brand__mark { width: 26px; height: 26px; display: block; }
  .card--front .brand { font-size: 27px; color: var(--white); }
  .card--front .brand__mark { background: var(--white); }
  .front__web {
    margin-top: 44px;
    font-family: "Questrial", sans-serif; font-size: 13px;
    letter-spacing: 0.42em; color: var(--white);
  }

  /* Back */
  .card--back { background: var(--paper); display: flex; }
  .back__brand-side {
    width: 52%; display: flex; align-items: center; justify-content: center;
  }
  .card--back .brand { font-size: 19px; color: var(--ink-navy); gap: 10px; }
  .card--back .brand__mark { width: 20px; height: 20px; background: var(--ink-navy); }
  .back__info {
    position: absolute; top: 14px; right: 14px; bottom: 18px; left: 52%;
    background: linear-gradient(120deg, var(--navy-mid) 0%, var(--navy-deep) 100%);
    color: var(--white);
    font-family: "Open Sans", sans-serif;
    display: flex; flex-direction: column; align-items: center; justify-content: center;
    text-align: center;
  }
  .back__info::after {
    content: ""; position: absolute; left: 0; right: 0; bottom: 12px;
    height: 2px; background: var(--white);
  }
  .contact__name {
    font-size: 15px; font-weight: 700; text-transform: uppercase; letter-spacing: 0.01em;
    margin-bottom: 16px;
  }
  .contact__address, .contact__links {
    font-size: 12.5px; line-height: 1.35; font-style: normal;
  }
  .contact__address { margin-bottom: 14px; }
</style>
</head>
<body>
  <main class="canvas">
    <section class="card card--front" aria-label="Business card front">
      <div class="brand">
        <span class="brand__mark" aria-hidden="true"></span>
        <span class="brand__name">Ferncliff Advisory</span>
      </div>
      <p class="front__web">www.ferncliffadvisory.com</p>
    </section>

    <section class="card card--back" aria-label="Business card back">
      <div class="back__brand-side">
        <div class="brand">
          <span class="brand__mark" aria-hidden="true"></span>
          <span class="brand__name">Ferncliff Advisory</span>
        </div>
      </div>
      <div class="back__info">
        <h1 class="contact__name">Daniel Whitcombe</h1>
        <address class="contact__address">
          2870 North 9th Avenue<br>
          Summit Floor, Elm Ridge<br>
          Illinois 60531
        </address>
        <p class="contact__links">
          dan@ferncliffadvisory.com<br>
          www.ferncliffadvisory.com
        </p>
      </div>
    </section>
  </main>
</body>
</html>
```